Lifecoach needs website design based on a standard Wordpress theme

I need a website for my new lifecoaching business that can be easily implemented in Wordpress, it needs to be compatible with a standard Wordpress theme. So I can place the pictures, texts etc. in a standard theme of Wordpress.

I want the design to be a very good feeling and playfull one, based on my logo.

Target Market(s)

I will coach people to reach their goals and dreams in life.

Industry/Entity Type

Business

Requirements
Must have
• Can be easy implemented in Wordpress.
Nice to have
• Photo's of nature are nice.

```html
<!DOCTYPE html>
<html lang="en">
<head>
<meta charset="utf-8">
<title>Tom Verhaar Lifecoach</title>
<link rel="stylesheet" href="https://fonts.googleapis.com/css2?family=Open+Sans:ital,wdth,wght@0,75..100,300..800;1,75..100,300..800&display=swap">
<style>
:root{
  --navy:#0b4f7e;
  --sky:#1aa7e0;
  --sky-light:#42c3f2;
  --text:#3a3a3a;
  --muted:#5b7690;
  --band:#1c6792;
  --band-top:#2f86b8;
  --page:#fafcfd;
  --line:#cfd6db;
}
*{margin:0;padding:0;box-sizing:border-box}
html,body{width:1024px;height:1200px;overflow:hidden;background:var(--page);font-family:"Open Sans",Arial,sans-serif;color:var(--text)}
.page{position:relative;width:1024px;height:1200px}
.abs{position:absolute}
.cond{font-family:"Open Sans",Arial,sans-serif;font-stretch:75%;font-weight:700}

/* header */
.header{top:0;left:0;width:1024px;height:88px;background:#fff}
.header-rule{top:88px;left:0;width:1024px;height:5px;background:var(--sky)}
.header-shadow{top:93px;left:120px;width:900px;height:40px;background:radial-gradient(ellipse at 50% 0,rgba(0,0,0,.18),rgba(0,0,0,0) 70%)}
.logo{top:8px;left:138px;display:flex;align-items:center;gap:10px}
.logo-mark{width:72px;height:72px;border-radius:50%;border:4px solid var(--sky);background:#fff}
.logo-name{font-size:21px;font-weight:600;color:var(--navy);line-height:1.1;letter-spacing:.5px}
.socials{top:19px;left:596px;display:flex;gap:6px}
.socials span{width:24px;height:24px;border-radius:3px}
.s1{background:#3b5a9a}.s2{background:#2aa3df}.s3{background:#0f6a9c}.s4{background:#d23a2c}
.btn{background:linear-gradient(#3cc2f0,#129fd8);color:#fff;border-radius:6px;font-weight:700;display:flex;align-items:center;justify-content:center;box-shadow:0 1px 2px rgba(0,0,0,.25);border:1px solid #0e8cc2}
.btn-top{top:10px;left:724px;width:168px;height:39px;font-size:12px}
.nav{top:54px;left:438px;display:flex;height:34px;font-size:12px;color:#6c7a86}
.nav a{display:flex;align-items:center;padding:0 12px;text-decoration:none;color:inherit;margin-right:18px}
.nav a.active{background:var(--sky);color:#fff;margin-right:20px}

/* hero */
.hero{top:93px;left:0;width:1024px;height:334px}
.hero-photo{position:absolute;inset:0;background:
  linear-gradient(180deg,rgba(250,252,253,1) 0%,rgba(250,252,253,.6) 35%,rgba(250,252,253,0) 60%),
  radial-gradient(ellipse at 72% 40%,#fff3c4 0%,#f2d77e 30%,rgba(0,0,0,0) 60%),
  linear-gradient(180deg,#f7f0d6 0%,#d9d49a 50%,#95a94b 75%,#5f8a2e 100%)}
.hero-rule{top:427px;left:0;width:1024px;height:4px;background:var(--navy)}
.hero-title{top:145px;left:138px;font-size:27px;line-height:32px;color:var(--navy)}
.hero-title em{font-style:normal;color:var(--sky)}
.hero-text{top:221px;left:138px;width:280px;font-size:13px;line-height:19px;color:#333}

/* services */
.service{width:250px}
.service .tick{position:absolute;left:0;top:0}
.service h3{position:absolute;left:33px;top:0;font-size:20px;color:var(--navy);white-space:nowrap;line-height:24px}
.service p{position:absolute;left:33px;top:34px;width:205px;font-size:11.5px;line-height:17px;color:var(--muted)}

/* welcome & testimonial */
.section-title{font-size:20px;color:var(--navy)}
.dots{height:0;border-top:3px dotted var(--line)}
.portrait{top:806px;left:139px;width:238px;height:167px;border-radius:3px;background:linear-gradient(90deg,#c8d4e0 0%,#e6dcd2 45%,#ececec 78%,#f4f4f4 100%)}
.welcome-text{top:819px;left:395px;width:230px;font-size:12px;line-height:19px;color:var(--muted)}
.welcome-text p{margin-bottom:19px}
.read-more{top:955px;left:395px;font-size:12px;font-weight:700;color:var(--sky);text-decoration:underline}
.avatar{top:808px;left:725px;width:69px;height:69px;border-radius:50%;background:radial-gradient(circle at 50% 45%,#caa38f,#5a3d32 75%);border:2px solid #e4e9ee}
.t-name{top:888px;left:660px;width:200px;text-align:center;font-size:12px;font-weight:700;color:#333}
.t-place{top:906px;left:660px;width:200px;text-align:center;font-size:10px;font-style:italic;color:#777}
.t-quote{top:926px;left:658px;width:210px;font-size:10px;line-height:16px;font-style:italic;color:var(--muted)}

/* CTA band */
.cta{top:1027px;left:0;width:1024px;height:79px;background:var(--band);border-top:4px solid var(--band-top)}
.cta-text{top:1052px;left:136px;font-size:20px;color:#fff}
.cta-text em{font-style:normal;color:#5fd0fa}
.btn-cta{top:1048px;left:695px;width:198px;height:41px;font-size:14px}

/* footer */
.f-socials{top:1127px;left:138px;display:flex;gap:11px}
.f-socials span{width:21px;height:21px;border-radius:50%}
.f1{background:#1f5c92}.f2{background:#2aa3df}.f3{background:#1f5c92}
.f-links{top:1132px;left:246px;font-size:10px;font-weight:700;letter-spacing:.8px;color:#5c6f82}
.f-links span{margin:0 7px;font-weight:400}
.copy{top:1157px;left:138px;font-size:10px;color:#6c7a86}
.contact{left:746px;font-size:10px;color:#5c6f82;display:flex;align-items:center;gap:12px}
</style>
</head>
<body>
<div class="page">

  <header>
    <div class="abs header"></div>
    <div class="abs logo">
      <div class="logo-mark"></div>
      <div class="logo-name">Tom Verhaar<br>Lifecoach</div>
    </div>
    <div class="abs socials"><span class="s1"></span><span class="s2"></span><span class="s3"></span><span class="s4"></span></div>
    <div class="abs btn btn-top">Request Coaching Session</div>
    <nav class="abs nav">
      <a class="active">Home</a><a>About</a><a>Coaching Services</a><a>Rates and Fees</a><a style="margin-right:0">Contact us</a>
    </nav>
    <div class="abs header-rule"></div>
  </header>

  <section class="abs hero">
    <div class="hero-photo" role="img" aria-label="Family of three running hand in hand through a sunlit grassy meadow"></div>
  </section>
  <div class="abs header-shadow"></div>
  <div class="abs hero-rule"></div>
  <h1 class="abs hero-title cond">Make A <em>Better Life</em> For You<br>and Your Family</h1>
  <p class="abs hero-text">Maecenas mauris velit, consequat sit amet pharetra ut, ultricies vitae mi. Duis tempus mattis sem id placerat. Sed et risus non erat</p>

  <section class="services">
    <div class="abs service" style="top:463px;left:138px">
      <svg class="tick" width="26" height="26" viewBox="0 0 26 26"><circle cx="13" cy="13" r="11.5" fill="none" stroke="#0b4f7e" stroke-width="2.5"/><path d="M7.5 13.5l4 4 7-8" fill="none" stroke="#0b4f7e" stroke-width="3" stroke-linecap="round" stroke-linejoin="round"/></svg>
      <h3 class="cond">Physical Issues</h3>
      <p>Praesent vitae purus eu libero laoreet ornare. Ut justo quam, et cursus neque. Fusce dui nibh auctor vel fermentum non condimentum vel...</p>
    </div>
    <div class="abs service" style="top:463px;left:393px">
      <svg class="tick" width="26" height="26" viewBox="0 0 26 26"><circle cx="13" cy="13" r="11.5" fill="none" stroke="#0b4f7e" stroke-width="2.5"/><path d="M7.5 13.5l4 4 7-8" fill="none" stroke="#0b4f7e" stroke-width="3" stroke-linecap="round" stroke-linejoin="round"/></svg>
      <h3 class="cond">Release of Blockages</h3>
      <p>Praesent vitae purus eu libero laoreet ornare. Ut justo quam, et cursus neque. Fusce dui nibh auctor vel fermentum non condimentum vel...</p>
    </div>
    <div class="abs service" style="top:463px;left:649px">
      <svg class="tick" width="26" height="26" viewBox="0 0 26 26"><circle cx="13" cy="13" r="11.5" fill="none" stroke="#0b4f7e" stroke-width="2.5"/><path d="M7.5 13.5l4 4 7-8" fill="none" stroke="#0b4f7e" stroke-width="3" stroke-linecap="round" stroke-linejoin="round"/></svg>
      <h3 class="cond">Bringing Your Life Into Balance</h3>
      <p>Praesent vitae purus eu libero laoreet ornare. Ut justo quam, et cursus neque. Fusce dui nibh auctor vel fermentum non condimentum vel...</p>
    </div>
    <div class="abs service" style="top:600px;left:138px">
      <svg class="tick" width="26" height="26" viewBox="0 0 26 26"><circle cx="13" cy="13" r="11.5" fill="none" stroke="#0b4f7e" stroke-width="2.5"/><path d="M7.5 13.5l4 4 7-8" fill="none" stroke="#0b4f7e" stroke-width="3" stroke-linecap="round" stroke-linejoin="round"/></svg>
      <h3 class="cond">Spiritual Growth</h3>
      <p>Praesent vitae purus eu libero laoreet ornare. Ut justo quam, et cursus neque. Fusce dui nibh auctor vel fermentum non condimentum vel...</p>
    </div>
    <div class="abs service" style="top:600px;left:393px">
      <svg class="tick" width="26" height="26" viewBox="0 0 26 26"><circle cx="13" cy="13" r="11.5" fill="none" stroke="#0b4f7e" stroke-width="2.5"/><path d="M7.5 13.5l4 4 7-8" fill="none" stroke="#0b4f7e" stroke-width="3" stroke-linecap="round" stroke-linejoin="round"/></svg>
      <h3 class="cond">Emotional Issues</h3>
      <p>Praesent vitae purus eu libero laoreet ornare. Ut justo quam, et cursus neque. Fusce dui nibh auctor vel fermentum non condimentum vel...</p>
    </div>
    <div class="abs service" style="top:600px;left:649px">
      <svg class="tick" width="26" height="26" viewBox="0 0 26 26"><circle cx="13" cy="13" r="11.5" fill="none" stroke="#0b4f7e" stroke-width="2.5"/><path d="M7.5 13.5l4 4 7-8" fill="none" stroke="#0b4f7e" stroke-width="3" stroke-linecap="round" stroke-linejoin="round"/></svg>
      <h3 class="cond">Mental Issues</h3>
      <p>Praesent vitae purus eu libero laoreet ornare. Ut justo quam, et cursus neque. Fusce dui nibh auctor vel fermentum non condimentum vel...</p>
    </div>
  </section>

  <section class="welcome">
    <h2 class="abs section-title cond" style="top:754px;left:140px">Welcome to Our Site</h2>
    <div class="abs dots" style="top:792px;left:138px;width:480px"></div>
    <div class="abs portrait" role="img" aria-label="Portrait photo of the life coach"></div>
    <div class="abs welcome-text">
      <p>Lorem ipsum dolor sit amet, consectetur adipisicing elit, sed do eiusmod</p>
      <p>Tempor incididunt ut labore et dolore magna aliqua. Ut enim ad minim veniam, quis nostrud exercitation.</p>
    </div>
    <a class="abs read-more">READ MORE</a>
  </section>

  <section class="testimonial">
    <h2 class="abs section-title cond" style="top:754px;left:649px">Client Testimonial</h2>
    <div class="abs dots" style="top:792px;left:647px;width:240px"></div>
    <div class="abs avatar" role="img" aria-label="Client portrait photo"></div>
    <div class="abs t-name">Mara Lindqvist</div>
    <div class="abs t-place">Lyon, France</div>
    <p class="abs t-quote">“Lorem ipsum dolor sit amet, consectetur adipisicing elit, sed do eiusmod tempor incidi-dunt ut labore et dolore magna aliqua.</p>
  </section>

  <section>
    <div class="abs cta"></div>
    <div class="abs cta-text cond">Call us at <em>+1800.5550.2718</em> or Book a Private Coaching Session Now</div>
    <div class="abs btn btn-cta">Request Coaching Session</div>
  </section>

  <footer>
    <div class="abs f-socials"><span class="f1"></span><span class="f2"></span><span class="f3"></span></div>
    <div class="abs f-links">LINKS<span>|</span>LINKS<span>|</span>LINKS<span>|</span>LINKS</div>
    <div class="abs copy">Copyright © 2014 All rights reserved.&nbsp; Company Name</div>
    <div class="abs contact" style="top:1130px">
      <svg width="16" height="12" viewBox="0 0 16 12"><rect x="0" y="0" width="16" height="12" rx="1" fill="#7c8791"/><path d="M0.5 1l7.5 6 7.5-6" fill="none" stroke="#fafcfd" stroke-width="1.3"/></svg>
      hello@verhaarcoaching.com
    </div>
    <div class="abs contact" style="top:1154px">
      <svg width="16" height="14" viewBox="0 0 16 14"><path d="M3 1c1-.6 1.7-.3 2.2.6l1 1.9c.3.7.1 1.2-.5 1.6l-.8.5c.7 1.6 1.9 2.8 3.5 3.6l.5-.8c.4-.6.9-.8 1.6-.5l1.9 1c.9.5 1.1 1.2.6 2.1-.7 1.2-2 1.6-3.3 1.1C5.9 11.8 3.1 9.1 1.7 5.3 1.2 3.9 1.7 1.8 3 1z" fill="#7c8791"/></svg>
      555-01234-67890
    </div>
  </footer>

</div>
</body>
</html>
```